Existing Website Requiring new Pages

I have an existing word press website that was built using elementor.
Website: www.tallowcrestcare.com.au
I require the Vacancies page (https://www.tallowcrestcare.com.au/vacancies/) to be modified to display our new properties along with minor tweaks to how the information is presented.
The vacancies to be displayed are the exactly the same as those that are located on the homepage of Quarrymere website (https://qmr.org.au/)
The new pages that link off the Vacancies tab will require custom design.
There are roughly 8 pages/properties to be incorporated. i wish for the design to be very similar to that displayed in the following link; https://www.polunda.com.au/vacancies/merrylands
Along with this the back end has not been updated for the last 3 years so it also requires some maintenance.
Website is in the disability industry and the custom pages will display information relative to Property Vacancies.
I have attached a ZIP file with some design guides, the information for each of the properties (which will need to be modified to show our business name Tallowcrest Care) and the example of how it is to look based off the Polunda website.
If you guys have any suggestions or ideas on how to make this more presentable or possible i'm open to your ideas.
Target Market(s)
People looking for SDA properties custom built for people with a disability
Industry/Entity Type
Disability
Coding
Coded - Design and coding required
Number of Pages Required
5+ page

```html
<!DOCTYPE html>
<html lang="en">
<head>
<meta charset="utf-8">
<title>Tallowcrest Care – SDA Vacancies</title>
<link href="https://fonts.googleapis.com/css2?family=Montserrat:wght@400;500;600&family=Lato:wght@400;700&display=swap" rel="stylesheet">
<style>
:root{
  --coral:#f47a60;
  --coral-soft:#fde9e4;
  --ink:#1f1f1f;
  --text:#555;
  --muted:#8a8a8a;
  --line:#e4e4e4;
  --footer-bg:#f5f5f5;
  --white:#fff;
}
*{box-sizing:border-box;margin:0;padding:0}
html,body{width:1200px;height:2932px;overflow:hidden}
body{font-family:'Lato',sans-serif;color:var(--text);background:var(--footer-bg);position:relative}
.page{position:absolute;left:0;top:0;width:1200px;height:2524px;background:var(--white);border-radius:0 0 56px 56px}
.abs{position:absolute}

/* header */
.brand{left:92px;top:40px;display:flex;align-items:center;gap:8px;font-family:'Montserrat',sans-serif;font-weight:600;font-size:15px;color:var(--coral)}
.brand-dot{width:14px;height:14px;border-radius:50%;background:var(--coral)}
.nav{left:367px;top:41px;display:flex;gap:30px;font-family:'Montserrat',sans-serif;font-size:12px;font-weight:500;color:var(--ink)}
.nav .active{color:var(--coral);display:flex;align-items:center;gap:8px}
.btn{background:var(--coral);color:#fff;border-radius:6px;display:flex;align-items:center;justify-content:center;font-family:'Montserrat',sans-serif}
.contact-btn{left:981px;top:26px;width:127px;height:45px;font-size:12px}

/* hero */
.hero-title{left:92px;top:170px;font-family:'Montserrat',sans-serif;font-weight:500;font-size:43px;color:var(--ink)}
.hero-copy{left:92px;top:229px;width:523px;font-size:13.5px;line-height:21.6px;text-align:justify}
.explore{left:92px;top:332px;width:136px;height:48px;font-size:15px;font-family:'Lato',sans-serif}
.search{left:92px;top:405px;width:523px;height:72px;background:#fff;border-radius:6px;box-shadow:0 6px 28px rgba(0,0,0,.08);display:flex;align-items:center;padding:0 17px}
.field{width:148px}
.field small{display:block;font-size:9.5px;color:var(--coral);margin-bottom:5px}
.field div{display:flex;justify-content:space-between;align-items:center;font-size:13px;color:#444;padding-right:8px}
.search-go{width:48px;height:48px;margin-left:auto;border-radius:5px}
.hero-media{left:682px;top:142px;width:426px;height:365px;border-radius:4px;background:linear-gradient(160deg,#cfd7dc 0%,#8e9a8f 45%,#6f7f55 75%,#a77d5e 100%)}
.arrow{width:44px;height:44px;border-radius:50%;background:rgba(255,255,255,.55)}
.arrow.next{background:rgba(255,255,255,.85)}

/* properties */
.kicker{left:0;width:1200px;top:576px;text-align:center;font-family:'Montserrat',sans-serif;font-size:19px;color:var(--coral)}
.section-title{left:0;width:1200px;top:605px;text-align:center;font-family:'Montserrat',sans-serif;font-weight:500;font-size:28px;color:var(--ink)}
.map{left:92px;top:669px;width:1016px;height:447px;border-radius:4px;background:linear-gradient(135deg,#e3efe3 0%,#f1f1ef 35%,#efefed 70%,#e6eef5 100%)}
.grid{left:92px;top:1150px;width:1016px;display:grid;grid-template-columns:repeat(3,317px);column-gap:33px;row-gap:31px}
.card-media{position:relative;height:235px;border-radius:4px}
.tone-a{background:linear-gradient(170deg,#8fb6da 0%,#c9b79a 55%,#7a8c5a 100%)}
.tone-b{background:linear-gradient(170deg,#a9c3dc 0%,#6e5b52 50%,#6f6e6b 100%)}
.tone-c{background:linear-gradient(170deg,#d7dde0 0%,#6b6b68 55%,#8d8f8a 100%)}
.tone-d{background:linear-gradient(170deg,#7fa6cf 0%,#3c4046 55%,#b6b4ae 100%)}
.tone-e{background:linear-gradient(170deg,#7fa8d6 0%,#9e7a63 50%,#6f9a48 100%)}
.tone-f{background:linear-gradient(170deg,#5d6166 0%,#b9aa95 50%,#4b3a31 100%)}
.status{position:absolute;left:14px;top:14px;background:var(--coral);color:#fff;font-size:9px;padding:5px 6px;border-radius:3px}
.place{margin-top:22px;display:flex;align-items:center;gap:7px;font-size:9.5px;color:#666}
.card-title{margin-top:8px;font-family:'Montserrat',sans-serif;font-weight:500;font-size:21px;color:var(--ink)}
.card-copy{margin-top:6px;font-size:13px;line-height:21.6px;text-align:justify;color:#666}
.tags{margin-top:16px;display:flex;flex-wrap:wrap;gap:9px}
.tag{height:27px;padding:0 9px;border-radius:4px;background:var(--coral-soft);color:#888;font-size:9.5px;display:flex;align-items:center;gap:8px}

/* footer */
.f-brand{left:95px;top:2640px;font-family:'Montserrat',sans-serif;font-weight:600;font-size:26px;color:var(--coral);display:flex;align-items:center;gap:10px}
.f-brand span{width:22px;height:22px;border-radius:50%;background:var(--coral)}
.f-contact{left:92px;top:2748px;display:flex;flex-direction:column;gap:9px;font-size:10px;color:#444}
.f-contact div{display:flex;align-items:center;gap:10px}
.f-icon{width:26px;height:26px;border-radius:50%;background:var(--coral);display:flex;align-items:center;justify-content:center}
.f-head{font-family:'Montserrat',sans-serif;font-weight:500;font-size:15.5px;color:var(--ink);border-left:4px solid var(--coral);padding-left:13px;line-height:22px}
.f-list{list-style:none;margin-top:12px;font-size:10.5px;color:#555}
.f-list li{padding:10px 0;border-bottom:1px solid var(--line)}
.f-list li:last-child{border-bottom:0}
.social{display:flex;gap:10px;margin-top:14px}
.social span{width:28px;height:28px;border-radius:50%;background:#2b3a73}
.social span:first-child{background:#6b3b86}
.social span:nth-child(3){background:#222}
.social span:nth-child(4){background:#1f6fb2}
.email{margin-top:12px;width:252px;height:40px;background:#ececec;border-radius:3px;font-size:10.5px;color:#999;padding:0 12px;display:flex;align-items:center}
.subscribe{margin-top:11px;width:252px;height:40px;font-size:11px;font-family:'Lato',sans-serif}
.rule{left:92px;top:2878px;width:1016px;height:1px;background:#ddd}
.copy{left:0;width:1200px;top:2900px;text-align:center;font-size:10.5px;color:#888}
</style>
</head>
<body>
<div class="page">
  <header>
    <div class="abs brand"><span class="brand-dot"></span>Tallowcrest Care</div>
    <nav class="abs nav">
      <span>HOME</span><span>ABOUT US</span>
      <span class="active">WHAT WE DO <svg width="10" height="6" viewBox="0 0 10 6"><path d="M1 1l4 4 4-4" fill="none" stroke="#f47a60" stroke-width="1.4"/></svg></span>
      <span>REFERRALS</span><span>FEEDBACK</span>
    </nav>
    <div class="abs btn contact-btn">CONTACT US</div>
  </header>

  <section class="hero">
    <h1 class="abs hero-title">Tallowcrest Care</h1>
    <p class="abs hero-copy">Tallowcrest Care is a Sydney based disability support services provider. Focusing on intellectual, physical &amp; sensory disabilities including mental health within the Greater Sydney region, we strive to assist our participants in leading an independent and fulfilling life.</p>
    <div class="abs btn explore">Explore Now</div>
    <form class="abs search">
      <div class="field"><small>Current or future</small><div>Both <svg width="10" height="6"><path d="M1 1l4 4 4-4" fill="none" stroke="#555" stroke-width="1.3"/></svg></div></div>
      <div class="field"><small>Design category</small><div>All categories <svg width="10" height="6"><path d="M1 1l4 4 4-4" fill="none" stroke="#555" stroke-width="1.3"/></svg></div></div>
      <div class="field"><small>Location</small><div>All suburbs <svg width="10" height="6"><path d="M1 1l4 4 4-4" fill="none" stroke="#555" stroke-width="1.3"/></svg></div></div>
      <div class="btn search-go"><svg width="18" height="18" viewBox="0 0 18 18"><circle cx="7.5" cy="7.5" r="5.5" fill="none" stroke="#fff" stroke-width="2"/><path d="M11.5 11.5l5 5" stroke="#fff" stroke-width="2"/></svg></div>
    </form>
    <div class="abs hero-media" role="img" aria-label="Modern home exterior with timber deck and pergola">
      <div class="abs arrow" style="left:301px;top:300px"><svg width="44" height="44"><path d="M27 22H17M21 17l-5 5 5 5" fill="none" stroke="#f47a60" stroke-width="1.6"/></svg></div>
      <div class="abs arrow next" style="left:359px;top:300px"><svg width="44" height="44"><path d="M17 22h10M23 17l5 5-5 5" fill="none" stroke="#f47a60" stroke-width="1.6"/></svg></div>
    </div>
  </section>

  <section class="properties">
    <p class="abs kicker">Our Properties</p>
    <h2 class="abs section-title">View Our SDA Vacancies and Homes Being Built</h2>
    <div class="abs map" role="img" aria-label="Street map of Glenmore Park showing property locations"></div>

    <div class="abs grid">
      <article class="card">
        <div class="card-media tone-a" role="img" aria-label="Two-storey SDA home in Greystanes"><span class="status">Almost Full</span></div>
        <p class="place"><svg width="9" height="12" viewBox="0 0 9 12"><path d="M4.5 0A4.5 4.5 0 0 0 0 4.5C0 8 4.5 12 4.5 12S9 8 9 4.5A4.5 4.5 0 0 0 4.5 0z" fill="#f47a60"/><circle cx="4.5" cy="4.5" r="1.6" fill="#fff"/></svg>Greystanes</p>
        <h3 class="card-title">SDA in Greystanes</h3>
        <p class="card-copy">Accessible and High Support SDA Apartments in Greystanes for NDIS Participants.</p>
        <div class="tags"><span class="tag"><svg width="14" height="10"><rect x="0" y="3" width="14" height="5" rx="1" fill="#777"/><rect x="1" y="0" width="5" height="3" fill="#777"/></svg>6 x 1 bedroom FA/HPS</span></div>
      </article>
      <article class="card">
        <div class="card-media tone-b" role="img" aria-label="Brick townhouse with garage in Jordan Springs"><span class="status">Available Now</span></div>
        <p class="place"><svg width="9" height="12" viewBox="0 0 9 12"><path d="M4.5 0A4.5 4.5 0 0 0 0 4.5C0 8 4.5 12 4.5 12S9 8 9 4.5A4.5 4.5 0 0 0 4.5 0z" fill="#f47a60"/><circle cx="4.5" cy="4.5" r="1.6" fill="#fff"/></svg>Jordan Springs</p>
        <h3 class="card-title">SDA in Jordan Springs</h3>
        <p class="card-copy">Accessible and Improved Liveability SDA Apartments in Jordan Springs for NDIS Participants.</p>
        <div class="tags"><span class="tag"><svg width="14" height="10"><rect x="0" y="3" width="14" height="5" rx="1" fill="#777"/><rect x="1" y="0" width="5" height="3" fill="#777"/></svg>2 bedrooms improved liveability</span><span class="tag"><svg width="14" height="10"><rect x="0" y="3" width="14" height="5" rx="1" fill="#777"/><rect x="1" y="0" width="5" height="3" fill="#777"/></svg>2 bedrooms FA</span></div>
      </article>
      <article class="card">
        <div class="card-media tone-c" role="img" aria-label="Row of modern townhouses in Werrington"><span class="status">Available Now</span></div>
        <p class="place"><svg width="9" height="12" viewBox="0 0 9 12"><path d="M4.5 0A4.5 4.5 0 0 0 0 4.5C0 8 4.5 12 4.5 12S9 8 9 4.5A4.5 4.5 0 0 0 4.5 0z" fill="#f47a60"/><circle cx="4.5" cy="4.5" r="1.6" fill="#fff"/></svg>Werrington</p>
        <h3 class="card-title">SDA in Werrington</h3>
        <p class="card-copy">Quarrymere Residences is a charity with extensive experience in SDA.</p>
        <div class="tags"><span class="tag"><svg width="14" height="10"><rect x="0" y="3" width="14" height="5" rx="1" fill="#777"/><rect x="1" y="0" width="5" height="3" fill="#777"/></svg>1 bedroom improved liveability</span><span class="tag"><svg width="14" height="10"><rect x="0" y="3" width="14" height="5" rx="1" fill="#777"/><rect x="1" y="0" width="5" height="3" fill="#777"/></svg>2 bedrooms FA</span></div>
      </article>

      <article class="card">
        <div class="card-media tone-d" role="img" aria-label="Single-storey dark brick villas in Wentworthville"><span class="status">Available Now</span></div>
        <p class="place"><svg width="9" height="12" viewBox="0 0 9 12"><path d="M4.5 0A4.5 4.5 0 0 0 0 4.5C0 8 4.5 12 4.5 12S9 8 9 4.5A4.5 4.5 0 0 0 4.5 0z" fill="#f47a60"/><circle cx="4.5" cy="4.5" r="1.6" fill="#fff"/></svg>Wentworthville</p>
        <h3 class="card-title">SDA villas in Wentworthville</h3>
        <p class="card-copy">Quarrymere is proud to offer 8 SDA villas in Wentworthville to participants with SDA in their NDIS plans.</p>
        <div class="tags"><span class="tag"><svg width="14" height="10"><rect x="0" y="3" width="14" height="5" rx="1" fill="#777"/><rect x="1" y="0" width="5" height="3" fill="#777"/></svg>3 x 1 bedroom HPS/FA</span><span class="tag"><svg width="14" height="10"><rect x="0" y="3" width="14" height="5" rx="1" fill="#777"/><rect x="1" y="0" width="5" height="3" fill="#777"/></svg>1 x 2 bedroom HPS/FA</span><span class="tag"><svg width="14" height="10"><rect x="0" y="3" width="14" height="5" rx="1" fill="#777"/><rect x="1" y="0" width="5" height="3" fill="#777"/></svg>4 x 1 bedroom improved liveability</span></div>
      </article>
      <article class="card">
        <div class="card-media tone-c" role="img" aria-label="Townhouse with garage in West Pennant Hills"><span class="status">Available Now</span></div>
        <p class="place"><svg width="9" height="12" viewBox="0 0 9 12"><path d="M4.5 0A4.5 4.5 0 0 0 0 4.5C0 8 4.5 12 4.5 12S9 8 9 4.5A4.5 4.5 0 0 0 4.5 0z" fill="#f47a60"/><circle cx="4.5" cy="4.5" r="1.6" fill="#fff"/></svg>West Pennant Hills</p>
        <h3 class="card-title">SDA in West Pennant Hills</h3>
        <p class="card-copy">Accessible High Physical Support Apartments in West Pennant Hills for NDIS SDA participants.</p>
        <div class="tags"><span class="tag"><svg width="14" height="10"><rect x="0" y="3" width="14" height="5" rx="1" fill="#777"/><rect x="1" y="0" width="5" height="3" fill="#777"/></svg>6 x 1 bedroom HPS/FA</span><span class="tag"><svg width="14" height="10"><rect x="0" y="3" width="14" height="5" rx="1" fill="#777"/><rect x="1" y="0" width="5" height="3" fill="#777"/></svg>1 x 2 bedroom HPS/FA</span></div>
      </article>
      <article class="card">
        <div class="card-media tone-e" role="img" aria-label="Villas and apartments in Austral"><span class="status">Register Your Interest Today</span></div>
        <p class="place"><svg width="9" height="12" viewBox="0 0 9 12"><path d="M4.5 0A4.5 4.5 0 0 0 0 4.5C0 8 4.5 12 4.5 12S9 8 9 4.5A4.5 4.5 0 0 0 4.5 0z" fill="#f47a60"/><circle cx="4.5" cy="4.5" r="1.6" fill="#fff"/></svg>Austral</p>
        <h3 class="card-title">SDA in Austral</h3>
        <p class="card-copy">Accessible, High Support Apartments, and Robust Villas in Austral for NDIS Participants.</p>
        <div class="tags"><span class="tag"><svg width="14" height="10"><rect x="0" y="3" width="14" height="5" rx="1" fill="#777"/><rect x="1" y="0" width="5" height="3" fill="#777"/></svg>2 x 1 bedroom HPS/FA</span><span class="tag"><svg width="14" height="10"><rect x="0" y="3" width="14" height="5" rx="1" fill="#777"/><rect x="1" y="0" width="5" height="3" fill="#777"/></svg>1 x 2 bedroom HPS/FA</span><span class="tag"><svg width="14" height="10"><rect x="0" y="3" width="14" height="5" rx="1" fill="#777"/><rect x="1" y="0" width="5" height="3" fill="#777"/></svg>2 x 1 bedroom Robust Villas</span></div>
      </article>

      <article class="card">
        <div class="card-media tone-f" role="img" aria-label="Accessible open-plan living and dining room"><span class="status">New Construction</span></div>
        <p class="place"><svg width="9" height="12" viewBox="0 0 9 12"><path d="M4.5 0A4.5 4.5 0 0 0 0 4.5C0 8 4.5 12 4.5 12S9 8 9 4.5A4.5 4.5 0 0 0 4.5 0z" fill="#f47a60"/><circle cx="4.5" cy="4.5" r="1.6" fill="#fff"/></svg>Guildford West</p>
        <h3 class="card-title">SDA in Guildford West</h3>
        <p class="card-copy">Accessible and High Support SDA Apartments in Guildford West for NDIS Participants.</p>
        <div class="tags"><span class="tag"><svg width="14" height="10"><rect x="0" y="3" width="14" height="5" rx="1" fill="#777"/><rect x="1" y="0" width="5" height="3" fill="#777"/></svg>4 x 1 bedroom HPS/FA</span><span class="tag"><svg width="14" height="10"><rect x="0" y="3" width="14" height="5" rx="1" fill="#777"/><rect x="1" y="0" width="5" height="3" fill="#777"/></svg>1 x 2 bedroom HPS/FA</span></div>
      </article>
      <article class="card">
        <div class="card-media tone-c" role="img" aria-label="Townhouse with garage in Merrylands"><span class="status">Available Now</span></div>
        <p class="place"><svg width="9" height="12" viewBox="0 0 9 12"><path d="M4.5 0A4.5 4.5 0 0 0 0 4.5C0 8 4.5 12 4.5 12S9 8 9 4.5A4.5 4.5 0 0 0 4.5 0z" fill="#f47a60"/><circle cx="4.5" cy="4.5" r="1.6" fill="#fff"/></svg>Merrylands</p>
        <h3 class="card-title">SDA in Merrylands</h3>
        <p class="card-copy">Quarrymere’s Merrylands SDA offers Improved Liveability and High Physical Support.</p>
        <div class="tags"><span class="tag"><svg width="14" height="10"><rect x="0" y="3" width="14" height="5" rx="1" fill="#777"/><rect x="1" y="0" width="5" height="3" fill="#777"/></svg>1 bedroom HPS</span></div>
      </article>
      <article class="card">
        <div class="card-media tone-f" role="img" aria-label="Accessible open-plan living and dining room"><span class="status">Expression of Interest</span></div>
        <p class="place"><svg width="9" height="12" viewBox="0 0 9 12"><path d="M4.5 0A4.5 4.5 0 0 0 0 4.5C0 8 4.5 12 4.5 12S9 8 9 4.5A4.5 4.5 0 0 0 4.5 0z" fill="#f47a60"/><circle cx="4.5" cy="4.5" r="1.6" fill="#fff"/></svg>Guildford West</p>
        <h3 class="card-title">SDA in Blacktown</h3>
        <p class="card-copy">Brand new High Physical Support villas for NDIS participants with SDA funding.</p>
        <div class="tags"><span class="tag"><svg width="14" height="10"><rect x="0" y="3" width="14" height="5" rx="1" fill="#777"/><rect x="1" y="0" width="5" height="3" fill="#777"/></svg>6 x 1 bedroom HPS/FA</span></div>
      </article>
    </div>
  </section>
</div>

<footer>
  <div class="abs f-brand"><span></span>Tallowcrest Care</div>
  <div class="abs f-contact">
    <div><span class="f-icon"><svg width="12" height="12" viewBox="0 0 12 12"><path d="M2 1l2 0 1 3-1.5 1a7 7 0 0 0 3.5 3.5L8 7l3 1v2a1 1 0 0 1-1 1A9 9 0 0 1 1 2a1 1 0 0 1 1-1z" fill="#fff"/></svg></span>+61 0400 318 552</div>
    <div><span class="f-icon"><svg width="12" height="10"><rect x="0.5" y="0.5" width="11" height="9" rx="1" fill="none" stroke="#fff"/><path d="M1 1l5 4 5-4" fill="none" stroke="#fff"/></svg></span>info@tallowcrestcare.com.au</div>
    <div><span class="f-icon"><svg width="12" height="12"><circle cx="6" cy="6" r="5" fill="none" stroke="#fff" stroke-width="1.3"/><path d="M6 3v3l2 1" fill="none" stroke="#fff" stroke-width="1.3"/></svg></span>Operating Hours: 9AM to 5PM Moday - Friday</div>
  </div>

  <div class="abs" style="left:387px;top:2575px;width:210px">
    <h4 class="f-head">Accomodation</h4>
    <ul class="f-list"><li>Supported Independent Living (SIL)</li><li>Specialist Disability Accomodation (SDA)</li><li>Short Term Accomodtion (Respite)</li><li>Vacancies</li></ul>
    <h4 class="f-head" style="margin-top:22px">Contact Us</h4>
    <div class="social"><span></span><span></span><span></span><span></span></div>
  </div>
  <div class="abs" style="left:651px;top:2575px;width:150px">
    <h4 class="f-head">What We Do</h4>
    <ul class="f-list"><li>In Home Care</li><li>Social &amp; Community Services</li><li>Theraoeutic Supports</li><li>Support Coordination</li><li>Home Modifications</li></ul>
  </div>
  <div class="abs" style="left:856px;top:2575px;width:252px">
    <h4 class="f-head">Newsletter Subscription</h4>
    <div class="email">Write your email</div>
    <div class="btn subscribe">Subscribe</div>
  </div>

  <div class="abs rule"></div>
  <p class="abs copy">© Copyright 2021 - 2024 | Tallowcrest Care | All Rights Reserved.</p>
</footer>
</body>
</html>
```